TALMORK

The business want a professional looking business card. We have a scetch we will add but want the extra upgrade, and would like more suggestions for variations of our business cards.

```html
<!DOCTYPE html>
<html lang="en">
<head>
<meta charset="utf-8">
<title>TALMORK – Business Card</title>
<link rel="stylesheet" href="https://fonts.googleapis.com/css2?family=Cinzel:wght@500;600&family=Source+Sans+3:wght@400;600;700&family=Poppins:wght@400;500&display=swap">
<style>
  :root {
    --page: #ffffff;
    --card-dark: #030303;
    --gold: #d6b266;
    --gold-light: #ecd189;
    --gold-deep: #b98d40;
    --ink: #0b0b0b;
    --shadow: rgba(0, 0, 0, 0.28);
  }
  * { margin: 0; padding: 0; box-sizing: border-box; }
  html, body {
    width: 1200px; height: 1200px; overflow: hidden;
    background: var(--page);
  }
  .sheet { position: relative; width: 1200px; height: 1200px; }

  .card {
    position: absolute; left: 209px; width: 789px; height: 472px;
    box-shadow: 6px 8px 10px var(--shadow);
  }
  .card--front { top: 116px; background: var(--card-dark); color: var(--gold); }
  .card--back {
    top: 620px;
    background: linear-gradient(180deg,
      #e5bb58 0%, #f1d98e 12%, #f5e29a 23%, #e4ca8a 33%,
      #cdae6e 44%, #b89356 55%, #9d7435 72%, #b9975a 80%,
      #d9bf7f 90%, #f4df9a 100%);
  }

  /* front: company header */
  .company-name {
    position: absolute; left: 0; right: 0; top: 48px;
    text-align: center;
    font-family: "Cinzel", Georgia, serif; font-weight: 600;
    font-size: 37px; letter-spacing: 0.01em; color: var(--gold);
  }
  .divider { position: absolute; left: 50px; top: 92px; width: 689px; height: 22px; }
  .divider__line {
    position: absolute; left: 39px; right: 39px; top: 10px; height: 1.5px;
    background: var(--gold);
  }
  .divider__dot {
    position: absolute; left: 338px; top: 5px; width: 12px; height: 12px;
    border-radius: 50%; background: var(--gold-light);
  }
  .divider__ornament {
    position: absolute; top: 0; width: 36px; height: 22px; border-radius: 50%;
    background: linear-gradient(90deg, var(--gold-deep), var(--gold-light), var(--gold-deep));
  }
  .divider__ornament--left { left: 0; }
  .divider__ornament--right { right: 0; }

  /* front: person */
  .person { position: absolute; left: 50px; top: 205px; }
  .person__name {
    font-family: "Source Sans 3", Arial, sans-serif; font-weight: 700;
    font-size: 34px; line-height: 36px; color: var(--gold-light); letter-spacing: 0.005em;
  }
  .person__role {
    font-family: "Source Sans 3", Arial, sans-serif; font-weight: 400;
    font-size: 25px; line-height: 30px; color: var(--gold); margin-top: 1px;
  }
  .person__rule { width: 65px; height: 1.5px; background: var(--gold); margin-top: 13px; }

  .contacts {
    position: absolute; left: 50px; top: 320px; list-style: none;
    font-family: "Source Sans 3", Arial, sans-serif; font-size: 23px;
    color: var(--gold-light);
  }
  .contacts__item { display: flex; align-items: center; height: 37.5px; }
  .contacts__icon { width: 18px; height: 22px; margin-right: 15px; flex: none; }

  /* front: brand block */
  .brand-front { position: absolute; left: 430px; top: 212px; width: 350px; text-align: center; }
  .brand-front__mark {
    width: 86px; height: 86px; margin: 0 auto 54px;
    border: 3px solid var(--gold); border-radius: 50%;
  }
  .brand-front__name {
    font-family: "Cinzel", Georgia, serif; font-weight: 500;
    font-size: 40px; line-height: 44px; letter-spacing: 0.32em; margin-right: -0.32em;
    color: var(--gold-light);
  }
  .brand-front__since {
    margin-top: 5px;
    font-family: "Poppins", Arial, sans-serif; font-weight: 500;
    font-size: 14px; letter-spacing: 0.38em; margin-right: -0.38em; color: var(--gold-light);
  }

  /* back */
  .brand-back { position: absolute; left: 0; right: 0; top: 180px; text-align: center; color: var(--ink); }
  .brand-back__name {
    font-family: "Cinzel", Georgia, serif; font-weight: 500;
    font-size: 72px; line-height: 86px; letter-spacing: 0.2em; margin-right: -0.2em;
  }
  .brand-back__since {
    margin-top: 8px;
    font-family: "Poppins", Arial, sans-serif; font-weight: 500;
    font-size: 29px; letter-spacing: 0.45em; margin-right: -0.45em;
  }
</style>
</head>
<body>
<main class="sheet">

  <section class="card card--front" aria-label="Business card front">
    <h1 class="company-name">TALMORK AASVEEN</h1>
    <div class="divider">
      <span class="divider__ornament divider__ornament--left" role="img" aria-label="Decorative gold ornament"></span>
      <span class="divider__line"></span>
      <span class="divider__dot"></span>
      <span class="divider__ornament divider__ornament--right" role="img" aria-label="Decorative gold ornament"></span>
    </div>

    <div class="person">
      <p class="person__name">LARS HENRIK AASVEEN</p>
      <p class="person__role">CEO &amp; Founder</p>
      <div class="person__rule"></div>
    </div>

    <ul class="contacts">
      <li class="contacts__item">
        <svg class="contacts__icon" viewBox="0 0 18 22" aria-hidden="true">
          <rect x="3" y="1" width="12" height="20" rx="2" fill="none" stroke="#d6b266" stroke-width="2"/>
          <rect x="5" y="4" width="8" height="12" fill="#d6b266"/>
          <circle cx="9" cy="18.3" r="1.1" fill="#d6b266"/>
        </svg>
        <span>00 479 555 0142</span>
      </li>
      <li class="contacts__item">
        <svg class="contacts__icon" viewBox="0 0 18 22" aria-hidden="true">
          <rect x="0.5" y="5" width="17" height="12" fill="#d6b266"/>
          <path d="M0.5 5 L9 12 L17.5 5 M0.5 17 L7 11 M17.5 17 L11 11" fill="none" stroke="#030303" stroke-width="1.2"/>
        </svg>
        <span>talmork.llc@mailbox.com</span>
      </li>
      <li class="contacts__item">
        <svg class="contacts__icon" viewBox="0 0 18 22" aria-hidden="true">
          <g fill="none" stroke="#d6b266" stroke-width="1.3">
            <circle cx="9" cy="11" r="8"/>
            <ellipse cx="9" cy="11" rx="3.5" ry="8"/>
            <path d="M1 11 H17 M2.3 7 H15.7 M2.3 15 H15.7 M9 3 V19"/>
          </g>
        </svg>
        <span>www.talmork.llc</span>
      </li>
    </ul>

    <div class="brand-front">
      <div class="brand-front__mark"></div>
      <p class="brand-front__name">TALMORK</p>
      <p class="brand-front__since">SINCE 2026</p>
    </div>
  </section>

  <section class="card card--back" aria-label="Business card back">
    <div class="brand-back">
      <p class="brand-back__name">TALMORK</p>
      <p class="brand-back__since">SINCE 2026</p>
    </div>
  </section>

</main>
</body>
</html>
```